Ward Compass Business Card Design*

We need a business card design for our company Ward Compass. Our company is specialized in providing online consulting services regarding medical institutions, hospitals and doctors. We work with patients worldwide looking to choose between healthcare providers. We have a website you may use as a reference, where we list doctors and clinics worldwide. So we target Medical providers as well as patients worldwide.
Target Market(s)
Medical Providers and patients around the world
Industry/Entity Type
Medical
Contact Information for Business Card
Salwa Kettani
CEO
+90 612 348 2175
info@wardcompass.example
www.wardcompass.example
14 Annakhil 7 H.R.B. Rabat, Morocco
Requirements
Must have
- Company logo/name on one full side, personal info and smaller logo and company name on the other side.
Nice to have
- Smart and elegant design

```html
<!DOCTYPE html>
<html lang="en">
<head>
<meta charset="utf-8">
<title>Ward Compass – Business Card</title>
<link href="https://fonts.googleapis.com/css2?family=Montserrat:wght@500;600;700&family=Arimo:wght@400;700&display=swap" rel="stylesheet">
<style>
  :root {
    --backdrop: #d9d3cd;
    --card-face: #ebe8e5;
    --navy: #1b2b45;
    --ink-grey: #5a5d63;
    --text-dark: #2f3440;
  }
  * { margin: 0; padding: 0; box-sizing: border-box; }
  html, body {
    width: 1200px; height: 970px; overflow: hidden;
    background: var(--backdrop);
  }
  .canvas { position: relative; width: 1200px; height: 970px; }
  .card {
    position: absolute; left: 130px; top: 215px;
    width: 940px; height: 540px;
    background: var(--card-face);
    border-radius: 30px;
    overflow: hidden;
    box-shadow: 0 18px 40px rgba(40, 30, 20, 0.18);
  }
  .card__panel { position: absolute; inset: 0; }
  .brand {
    position: absolute; left: 56px; top: 108px;
    display: flex; align-items: center; gap: 18px;
  }
  .brand__dot {
    width: 70px; height: 70px; border-radius: 50%;
    background: var(--navy);
  }
  .brand__name {
    font-family: "Montserrat", sans-serif;
    font-weight: 600; font-size: 31px; letter-spacing: 0.5px;
    color: var(--navy);
  }
  .holder {
    position: absolute; left: 52px; top: 298px;
    font-family: "Arimo", sans-serif;
  }
  .holder__name { font-size: 28px; color: var(--ink-grey); letter-spacing: 0.5px; }
  .holder__name strong { color: var(--text-dark); font-weight: 700; }
  .holder__role { font-size: 21px; color: var(--ink-grey); margin-top: 4px; }
  .contacts {
    position: absolute; left: 52px; top: 432px;
    list-style: none;
    font-family: "Arimo", sans-serif; font-size: 20px; color: var(--text-dark);
  }
  .contacts li { display: flex; align-items: center; gap: 14px; height: 34px; }
  .contacts__icon {
    width: 26px; height: 26px; border-radius: 50%;
    background: var(--navy);
    display: flex; align-items: center; justify-content: center;
  }
  .contacts__icon svg { width: 14px; height: 14px; }
</style>
</head>
<body>
<div class="canvas">
  <div class="card">
    <svg class="card__panel" viewBox="0 0 940 540" aria-hidden="true">
      <path d="M650 0 H940 V540 H650 A280 280 0 0 1 650 0 Z" fill="var(--navy)"/>
    </svg>

    <div class="brand">
      <span class="brand__dot"></span>
      <span class="brand__name">WARD COMPASS</span>
    </div>

    <div class="holder">
      <p class="holder__name"><strong>SALWA</strong> KETTANI</p>
      <p class="holder__role">CEO</p>
    </div>

    <ul class="contacts">
      <li>
        <span class="contacts__icon">
          <svg viewBox="0 0 16 16"><path d="M4 1.5l2.2 3-1.3 1.5c.8 1.9 2.2 3.3 4.1 4.1l1.5-1.3 3 2.2-1.2 2.5C7 13.2 2.8 9 1.5 3.7z" fill="#fff"/></svg>
        </span>
        +90 612 348 2175
      </li>
      <li>
        <span class="contacts__icon">
          <svg viewBox="0 0 16 16"><rect x="1.5" y="3.5" width="13" height="9" rx="1" fill="none" stroke="#fff" stroke-width="1.5"/><path d="M2 4l6 5 6-5" fill="none" stroke="#fff" stroke-width="1.5"/></svg>
        </span>
        info@wardcompass.example
      </li>
      <li>
        <span class="contacts__icon">
          <svg viewBox="0 0 16 16"><circle cx="8" cy="8" r="6" fill="none" stroke="#fff" stroke-width="1.4"/><ellipse cx="8" cy="8" rx="2.6" ry="6" fill="none" stroke="#fff" stroke-width="1.2"/><path d="M2 8h12" stroke="#fff" stroke-width="1.2"/></svg>
        </span>
        www.wardcompass.example
      </li>
    </ul>
  </div>
</div>
</body>
</html>
```